Business Card and Letterhead for Pimlu - modern real estate business

I need a double sided business card design for Pimlu. Please see business card brief here https://files.trelvonadocs.com/sheet/r/7QzTmWbaXLJnoPEd-kRyUgFhHsstbvCe2qfoMxDa_pz/view?mode=shared

Please feel free to design the business cards however you feel best. I am happy to give some creative freedoms and then provide feedback from there.

Please then also create a letterhead to match the business card design

Colors

Designer to choose colors to be used in the design.

Requirements
Must have
• Must be a modern, elegant business card which looks very professional

```html
<!DOCTYPE html>
<html lang="en">
<head>
<meta charset="utf-8">
<title>Pimlu Letterhead</title>
<link rel="stylesheet" href="https://fonts.googleapis.com/css2?family=Montserrat:wght@400;500;800&family=Open+Sans:wght@400&display=swap">
<style>
  :root {
    --brand-red: #e30613;
    --backdrop: #a5b7bd;
    --paper: #ffffff;
    --ink: #1f1f1f;
    --body-ink: #555555;
    --rule: #444444;
    --signature-tone: #ececec;
  }
  * { box-sizing: border-box; margin: 0; padding: 0; }
  html, body { width: 1200px; height: 907px; overflow: hidden; }
  body { background: var(--backdrop); position: relative; font-family: "Open Sans", sans-serif; }

  .letterhead {
    position: absolute; left: 296px; top: 65px;
    width: 607px; height: 776px;
    background: var(--paper);
  }
  .brand-name {
    position: absolute; left: 46px; top: 16px;
    font-family: "Montserrat", sans-serif; font-weight: 800;
    font-size: 35px; letter-spacing: 1px; color: var(--brand-red);
  }
  .registration {
    position: absolute; right: 47px; top: 27px;
    font-family: "Montserrat", sans-serif; font-weight: 500;
    font-size: 9.5px; line-height: 12px; color: var(--ink);
  }
  .header-rule {
    position: absolute; left: 46px; right: 47px; top: 58px;
    border-top: 1px solid var(--rule);
  }
  .letter-date {
    position: absolute; left: 66px; top: 216px;
    font-size: 10px; color: var(--body-ink);
  }
  .letter-body {
    position: absolute; left: 66px; top: 265px; width: 490px;
    font-size: 9.6px; line-height: 20.4px; color: var(--body-ink);
  }
  .letter-body p { margin-bottom: 4px; }
  .letter-body span { display: block; white-space: nowrap; }
  .signature {
    position: absolute; left: 421px; top: 545px;
    width: 120px; height: 44px; background: var(--signature-tone);
    border-radius: 3px;
  }
  .signatory {
    position: absolute; left: 423px; top: 584px;
    font-family: "Montserrat", sans-serif; font-size: 9.5px; line-height: 12px; color: var(--ink);
  }
  .footer-rule {
    position: absolute; left: 46px; right: 47px; top: 730px;
    border-top: 1px solid var(--rule);
  }
  .contact-icons {
    position: absolute; left: 284px; top: 724px; display: flex; gap: 2px;
  }
  .contact-line {
    position: absolute; left: 0; right: 0; top: 738px;
    text-align: center; font-family: "Montserrat", sans-serif;
    font-size: 9.5px; color: var(--ink); word-spacing: 1px;
  }
  .contact-line span { margin: 0 6px; }
  .address-band {
    position: absolute; left: 0; right: 0; bottom: 0; height: 18px;
    background: var(--brand-red); color: var(--paper);
    font-family: "Montserrat", sans-serif; font-size: 9.5px;
    text-align: center; line-height: 18px;
  }
</style>
</head>
<body>
  <main class="letterhead">
    <div class="brand-name">PIMLU</div>
    <div class="registration">ABN: 48 219 805 364<br>Lic No. 20481736</div>
    <div class="header-rule"></div>

    <div class="letter-date">Date, 10 September, 2020</div>

    <div class="letter-body">
      <p>
        <span>This is a sample letter that has been placed to demonstrate typing remat (Your Company). letterhead</span>
        <span>design. When positioned properly, it will serve to work in harmony with all other elements letterhead.</span>
        <span>This letterhead design is meant to project an image</span>
      </p>
      <p>
        <span>This letterhead design is meant project an image of professionalism reliability. By using simple aligen</span>
        <span>we have created a very spacious feeling. The simplicity suggest&nbsp; rengththe spaciousnes contributes h</span>
        <span>aesthetics the layout. These basic qualities along with the (Your Company)</span>
      </p>
      <p>
        <span>look and helps reinforce the (Your Company) brand. letterhead design is meant to project an image p</span>
        <span>design. When positioned properly, it will serve to work in harmony all the other elements letterhead.</span>
        <span>sionalism and reliability.</span>
      </p>
      <p>
        <span>This letterhead design is based on the (Form of your logo) form (Your Company) logo. Each stationery</span>
        <span>we have created a very spacious feeling. The simplicity suggests strength the spaciousnes contribute</span>
        <span>part of the (Form of your logo).</span>
      </p>
    </div>

    <div class="signature" role="img" aria-label="Handwritten signature of Daniel Orwick"></div>
    <div class="signatory">Daniel Orwick<br>Manager</div>

    <div class="footer-rule"></div>
    <svg class="contact-icons" width="38" height="12" viewBox="0 0 38 12" aria-hidden="true">
      <circle cx="6" cy="6" r="5.5" fill="var(--brand-red)"/>
      <path d="M3.8 3.3l1.2-.3.6 1.4-.7.6a4 4 0 0 0 1.9 1.9l.6-.7 1.4.6-.3 1.2C6 8 3.8 5.8 3.8 3.3z" fill="#fff"/>
      <circle cx="19" cy="6" r="5.5" fill="var(--brand-red)"/>
      <rect x="16" y="4" width="6" height="4" fill="#fff"/>
      <path d="M16 4l3 2.2L22 4" stroke="var(--brand-red)" stroke-width="0.7" fill="none"/>
      <circle cx="32" cy="6" r="5.5" fill="var(--brand-red)"/>
      <circle cx="32" cy="6" r="3" stroke="#fff" stroke-width="0.8" fill="none"/>
      <path d="M29 6h6M32 3c-1.3 1.8-1.3 4.2 0 6M32 3c1.3 1.8 1.3 4.2 0 6" stroke="#fff" stroke-width="0.6" fill="none"/>
    </svg>
    <div class="contact-line"><span>02 4186 3927</span><span>info@pimlu.com</span><span>www.pimlu.com</span></div>
    <div class="address-band">PO Box 1190, Larkmoor NSW 2790</div>
  </main>
</body>
</html>
```